Business Card Design for Online Gift Business

Business card design for a new online Canadian company called "Harlow & Brine Gift Boxes" selling modern and luxurious gift boxes for every occasion. Items are sourced locally from talented socially-responsible Canadian artisans. Each gift is elegantly presented in a keepsake wood box to ensure a lasting impression.

Industry/Entity Type

E-Commerce

Contact Information for Business Card

Marla Whitcombe, Proprietor
Larkfield, BC
250-555-0174
www.harlowandbrine.ca
hello@harlowandbrine.ca

Requirements
Must have
• Crafted with care, given with love
• Please also include the symbols for Facebook and Instagram
Nice to have
• **I have attached a few samples of background colors and font colors that I like. I hope this helps in a few directions to try.

```html
<!DOCTYPE html>
<html lang="en">
<head>
<meta charset="utf-8">
<title>Harlow &amp; Brine Gift Boxes — Business Card</title>
<link rel="stylesheet" href="https://fonts.googleapis.com/css2?family=Lato:wght@400&display=swap">
<style>
  :root {
    --backdrop: #aab4b7;
    --card: #ece5dc;
    --ink: #2a2320;
    --shadow: rgba(40, 50, 55, 0.28);
  }
  * { box-sizing: border-box; margin: 0; padding: 0; }
  html, body {
    width: 1200px;
    height: 824px;
    overflow: hidden;
    background: var(--backdrop);
  }
  body {
    font-family: "Lato", sans-serif;
    font-weight: 400;
    color: var(--ink);
  }
  .stage {
    width: 1200px;
    height: 824px;
    display: flex;
    align-items: center;
    justify-content: center;
    gap: 60px;
  }
  .card {
    width: 500px;
    height: 286px;
    background: var(--card);
    box-shadow: 0 10px 24px var(--shadow);
    display: flex;
    flex-direction: column;
    align-items: center;
    justify-content: center;
    text-align: center;
    text-transform: uppercase;
  }
  .brand-dot {
    width: 34px;
    height: 34px;
    border-radius: 50%;
    background: var(--ink);
    margin-bottom: 12px;
  }
  .holder-name {
    font-size: 17px;
    letter-spacing: 1px;
    line-height: 1.2;
  }
  .holder-role {
    font-size: 10px;
    letter-spacing: 1px;
    line-height: 1.3;
    margin-top: 2px;
  }
  .contact-line,
  .tagline {
    font-size: 11px;
    letter-spacing: 0.6px;
    line-height: 1.4;
    white-space: nowrap;
  }
  .contact-line { margin-top: 10px; }
  .tagline { margin-top: 3px; }
  .social {
    display: flex;
    gap: 6px;
    margin-top: 8px;
  }
  .social-dot {
    width: 14px;
    height: 14px;
    border: 1.2px solid var(--ink);
    border-radius: 50%;
  }
  .wordmark {
    font-size: 30px;
    letter-spacing: 6px;
    line-height: 1;
    white-space: nowrap;
  }
  .wordmark-sub {
    font-size: 11px;
    letter-spacing: 5px;
    margin-top: 10px;
  }
</style>
</head>
<body>
  <main class="stage">
    <section class="card card-back" aria-label="Business card, contact side">
      <div class="brand-dot"></div>
      <p class="holder-name">Marla Whitcombe</p>
      <p class="holder-role">Proprietor</p>
      <p class="contact-line">Larkfield, BC | 250-555-0174 | www.harlowandbrine.ca</p>
      <p class="tagline">Crafted with care, given with love</p>
      <div class="social" aria-label="Social media">
        <span class="social-dot"></span>
        <span class="social-dot"></span>
      </div>
    </section>

    <section class="card card-front" aria-label="Business card, brand side">
      <p class="wordmark">Harlow &amp; Brine</p>
      <p class="wordmark-sub">Gift Boxes</p>
    </section>
  </main>
</body>
</html>
```